Bright Harbor Painters Banner

Create a banner that displays and reinforces Bright Harbor Painters’ brand identity while promoting our interior painting services. The banner will be displayed at indoor venues through the winter. The design should be clean, professional, and visually recognizable to both new and returning customers. See attached design brief & logo source files.

```html
<!DOCTYPE html>
<html lang="en">
<head>
<meta charset="utf-8">
<title>Bright Harbor Painters – Interior Painting Banner</title>
<link rel="stylesheet" href="https://fonts.googleapis.com/css2?family=Michroma&family=Montserrat:wght@600;700;800&family=Roboto+Condensed:wght@700&display=swap">
<style>
  :root {
    --brand-green: #6e9155;
    --charcoal: #3d3d3f;
    --white: #ffffff;
    --backdrop: #e9ebe7;
  }
  * { margin: 0; padding: 0; box-sizing: border-box; }
  html, body {
    width: 1200px;
    height: 879px;
    overflow: hidden;
    background: var(--backdrop);
  }
  .banner {
    position: absolute;
    left: 0;
    top: 257px;
    width: 1200px;
    height: 364px;
    background: var(--white);
    overflow: hidden;
  }
  .banner-shapes {
    position: absolute;
    inset: 0;
  }
  .brand-lockup {
    position: absolute;
    left: 40px;
    top: 28px;
    display: flex;
    align-items: center;
    gap: 22px;
  }
  .brand-square {
    width: 78px;
    height: 78px;
    background: var(--charcoal);
  }
  .brand-name {
    font-family: "Montserrat", sans-serif;
    font-weight: 800;
    font-size: 48px;
    line-height: 1.02;
    color: var(--brand-green);
    text-transform: uppercase;
    letter-spacing: 0.01em;
  }
  .service-headline {
    position: absolute;
    left: 650px;
    top: 10px;
    width: 480px;
    font-family: "Michroma", sans-serif;
    font-weight: 400;
    font-size: 40px;
    line-height: 50px;
    letter-spacing: 0.1em;
    color: var(--white);
    -webkit-text-stroke: 1.5px var(--white);
    text-align: center;
  }
  .tagline {
    position: absolute;
    left: 0;
    width: 1200px;
    top: 188px;
    font-family: "Montserrat", sans-serif;
    font-weight: 700;
    font-size: 31px;
    letter-spacing: 0.06em;
    color: var(--charcoal);
    text-align: center;
    white-space: nowrap;
  }
  .service-list {
    position: absolute;
    left: 0;
    width: 1200px;
    top: 242px;
    font-family: "Montserrat", sans-serif;
    font-weight: 700;
    font-size: 32px;
    letter-spacing: 0.05em;
    word-spacing: 0.45em;
    color: var(--brand-green);
    text-align: center;
    white-space: nowrap;
  }
  .call-to-action {
    position: absolute;
    left: 18px;
    top: 312px;
    font-family: "Roboto Condensed", sans-serif;
    font-weight: 700;
    font-size: 37px;
    letter-spacing: 0.02em;
    color: var(--white);
    white-space: nowrap;
  }
  .website {
    position: absolute;
    left: 745px;
    width: 440px;
    top: 325px;
    font-family: "Montserrat", sans-serif;
    font-weight: 800;
    font-size: 27px;
    color: var(--white);
    text-align: center;
    white-space: nowrap;
  }
</style>
</head>
<body>
  <section class="banner">
    <svg class="banner-shapes" width="1200" height="364" viewBox="0 0 1200 364" aria-hidden="true">
      <polygon class="headline-panel" points="586,0 1200,0 1200,168 648,168" fill="var(--brand-green)"/>
      <polygon class="headline-edge" points="572,0 590,0 652,168 634,168" fill="var(--charcoal)"/>
      <polygon class="cta-bar" points="0,308 694,308 724,364 0,364" fill="var(--charcoal)"/>
      <polygon class="url-bar" points="718,322 1200,322 1200,364 742,364" fill="var(--brand-green)"/>
    </svg>

    <div class="brand-lockup">
      <span class="brand-square"></span>
      <p class="brand-name">Bright Harbor<br>Painters</p>
    </div>

    <h1 class="service-headline">INTERIOR<br>PAINTING<br>SERVICES</h1>

    <p class="tagline">Paint Smarter" "Trusted local professionals, since 2005"</p>
    <p class="service-list">Walls • Ceilings • Trim • Cabinets • Drywall Repair</p>

    <p class="call-to-action">Call to action: “Book a Free Estimate at</p>
    <p class="website">www.brightharborpaint.com</p>
  </section>
</body>
</html>
```